Stonebrace Business Card Design

The Stonebrace Co is an aggregate (crushing) equipment dealer serving Western Canadian provinces. Stonebrace is a distributor of aggregate equipment for different manufacturers.

We are looking to change and update the existing business card which has been used since the existence of the company. A copy of existing card has been attached for reference. The Stonebrace Co logo we want to remain the same and we want the green color to remain the same.

We are wanting something new with a different look. A refreshing card to show a new modern and updated look. No longer wanting to have the manufacturers on the back of the card but something more like our logo on the back of the card with a statement like "Rock-Solid Equipment"

ideas could be:
- card can be different colors on front and back
- front or reverse of the card could possibly be the green color with the logo in black

Target Market(s)

Owners of Aggregate/Crushing companies

Contact Information for Business Card

see above

Requirements
Must have
• - logo to remain same along with same font within logo
• - green color to remain same
Nice to have
• as noted above under project description
Should not have

```html
<!DOCTYPE html>
<html lang="en">
<head>
<meta charset="utf-8">
<title>The Stonebrace Co – Business Card</title>
<link rel="stylesheet" href="https://fonts.googleapis.com/css2?family=Arimo:wght@400;700&display=swap">
<style>
  :root {
    --brand-green: #8b960f;
    --charcoal: #231f20;
    --paper: #f5f5f4;
    --ink: #1e1e1e;
    --rule: #8a8a8a;
    --backdrop: #e4e2de;
  }
  * { box-sizing: border-box; margin: 0; padding: 0; }
  html, body {
    width: 1200px; height: 900px; overflow: hidden;
    background: var(--backdrop);
    font-family: "Arimo", Arial, sans-serif;
  }
  .sheet {
    width: 1200px; height: 900px;
    display: flex; flex-direction: column;
    align-items: center; justify-content: center; gap: 44px;
  }
  .card {
    position: relative;
    width: 640px; height: 366px;
    border-radius: 3px;
    overflow: hidden;
    box-shadow: 0 6px 18px rgba(0,0,0,0.15);
  }

  /* Back side */
  .card-back { background: var(--charcoal); }
  .card-back .brand-name {
    position: absolute; left: 0; right: 0; top: 120px;
    text-align: center;
    color: var(--brand-green);
    font-size: 38px; font-weight: 700; letter-spacing: 1px;
  }
  .card-back .tagline {
    position: absolute; left: 0; right: 0; top: 212px;
    text-align: center;
    color: #ffffff;
    font-size: 15px; font-weight: 700; letter-spacing: 2.5px;
  }

  /* Front side */
  .card-front { background: var(--paper); color: var(--ink); }
  .brand {
    position: absolute; right: 40px; top: 62px;
    display: flex; align-items: center; gap: 14px;
  }
  .brand-dot {
    width: 40px; height: 40px; border-radius: 50%;
    background: var(--brand-green);
  }
  .brand .brand-name {
    font-size: 26px; font-weight: 700; color: var(--charcoal);
  }
  .divider {
    position: absolute; left: 250px; right: 40px; top: 150px;
    height: 1px; background: var(--rule);
  }
  .person-name {
    position: absolute; left: 40px; top: 166px;
    color: var(--brand-green);
    font-size: 24px; font-weight: 400; letter-spacing: 0.3px;
  }
  .address {
    position: absolute; right: 40px; top: 166px;
    text-align: right; font-size: 14px; line-height: 19px;
  }
  .web {
    position: absolute; right: 40px; top: 214px;
    display: flex; align-items: center; gap: 10px;
    font-size: 14px; line-height: 19px; text-align: right;
  }
  .phones {
    position: absolute; left: 40px; top: 252px;
    display: flex; align-items: center; gap: 12px;
  }
  .phone-list { font-size: 18px; line-height: 21px; }
  .icon-badge {
    width: 40px; height: 40px; border-radius: 50%;
    background: var(--brand-green);
    display: flex; align-items: center; justify-content: center;
    flex: none;
  }
  .icon-badge.small { width: 32px; height: 32px; }
  .band-green {
    position: absolute; left: 0; bottom: 0;
    width: 72%; height: 12px; background: var(--brand-green);
  }
  .band-dark {
    position: absolute; right: 0; bottom: 0;
    width: 28%; height: 12px; background: var(--charcoal);
  }
</style>
</head>
<body>
<main class="sheet">
  <section class="card card-back" aria-label="Card back">
    <div class="brand-name">The Stonebrace Co</div>
    <div class="tagline">ROCK-SOLID EQUIPMENT</div>
  </section>

  <section class="card card-front" aria-label="Card front">
    <div class="brand">
      <span class="brand-dot"></span>
      <span class="brand-name">THE STONEBRACE CO.</span>
    </div>
    <div class="divider"></div>
    <div class="person-name">DALE MARSTEN</div>
    <div class="address">2216-48B Avenue<br>Nisku, Alberta T9E 1K2</div>
    <div class="web">
      <div>dale@stonebrace.com<br>www.stonebrace.ca</div>
      <span class="icon-badge small">
        <svg width="18" height="18" viewBox="0 0 24 24" fill="none" stroke="#fff" stroke-width="2">
          <circle cx="12" cy="12" r="9"/>
          <path d="M3 12h18M12 3c3 3 3 15 0 18M12 3c-3 3-3 15 0 18"/>
        </svg>
      </span>
    </div>
    <div class="phones">
      <span class="icon-badge">
        <svg width="22" height="22" viewBox="0 0 24 24" fill="#fff">
          <path d="M6.6 10.8a15 15 0 0 0 6.6 6.6l2.2-2.2a1 1 0 0 1 1-.25 11.4 11.4 0 0 0 3.6.57 1 1 0 0 1 1 1V20a1 1 0 0 1-1 1A17 17 0 0 1 3 4a1 1 0 0 1 1-1h3.5a1 1 0 0 1 1 1c0 1.25.2 2.45.57 3.57a1 1 0 0 1-.25 1z"/>
        </svg>
      </span>
      <div class="phone-list">780.555.0142<br>780.555.0187<br>780.555.0163</div>
    </div>
    <div class="band-green"></div>
    <div class="band-dark"></div>
  </section>
</main>
</body>
</html>
```